Business cards - BRENT Roofing & Siding

We need simple business cards made up for our Roofing & Siding business based in Calgary Alberta.
The logo on one side of the card and potentially our slogan "Built with trust, verified by time".
The other side could have:
-A small logo
-Rep name:
-Rep cell phone:
-Rep email:
-Office phone: 403-684-2093
-Website: PrairieShingleWorks.com

We would like to incorporate the colours from our logo, especially the lite blue on the jpeg file. I have attached the ai file and jpeg file. We like the colours better on the jpeg file.

I do not require a money back guarantee

```html
<!DOCTYPE html>
<html lang="en">
<head>
<meta charset="utf-8">
<title>BRENT Roofing &amp; Siding – Business Cards</title>
<link rel="stylesheet" href="https://fonts.googleapis.com/css2?family=Arimo:wght@400;700&display=swap">
<style>
  :root {
    --backdrop: #e4e4e2;
    --card-charcoal: #363636;
    --brand-red: #ec1e24;
    --brand-blue: #3f7fc2;
    --ink-white: #ffffff;
    --emboss-grey: #4b4b4b;
  }
  * { box-sizing: border-box; margin: 0; padding: 0; }
  html, body {
    width: 1200px;
    height: 801px;
    overflow: hidden;
    background: var(--backdrop);
    font-family: "Arimo", Arial, sans-serif;
  }
  .sheet {
    position: relative;
    width: 1200px;
    height: 801px;
    display: flex;
    align-items: center;
    justify-content: center;
    gap: 40px;
  }
  .card {
    position: relative;
    width: 540px;
    height: 309px;
    background: var(--card-charcoal);
    overflow: hidden;
  }

  /* ---------- front ---------- */
  .contact-band {
    position: absolute;
    left: 0;
    right: 0;
    bottom: 0;
    height: 108px;
    background: var(--brand-red);
  }
  .accent-rule {
    position: absolute;
    left: 0;
    right: 0;
    bottom: 108px;
    height: 6px;
    background: var(--brand-blue);
  }
  .card-front .wordmark {
    position: absolute;
    left: 34px;
    top: 62px;
    color: var(--ink-white);
    font-weight: 400;
  }
  .wordmark .wordmark-name {
    display: block;
    font-size: 62px;
    letter-spacing: 6px;
    line-height: 1;
  }
  .wordmark .wordmark-trade {
    display: block;
    font-size: 17px;
    letter-spacing: 6px;
    text-transform: uppercase;
    margin-top: 8px;
  }
  .rep {
    position: absolute;
    right: 30px;
    top: 28px;
    text-align: right;
  }
  .rep-name {
    color: var(--brand-red);
    font-size: 15px;
    letter-spacing: 0.5px;
  }
  .rep-title {
    color: var(--ink-white);
    font-size: 13px;
    margin-top: 3px;
  }
  .contact-list {
    position: absolute;
    left: 22px;
    bottom: 14px;
    list-style: none;
    color: var(--ink-white);
    font-size: 13.5px;
    line-height: 20px;
  }
  .contact-list li {
    display: flex;
    align-items: center;
    gap: 9px;
  }
  .contact-list svg {
    width: 12px;
    height: 12px;
    flex: none;
  }

  /* ---------- back ---------- */
  .card-back {
    display: flex;
    align-items: center;
    justify-content: center;
  }
  .emboss-mark {
    text-align: center;
    color: var(--emboss-grey);
    font-weight: 400;
  }
  .emboss-mark .est {
    display: block;
    font-size: 13px;
    letter-spacing: 4px;
    margin-bottom: 6px;
  }
  .emboss-mark .wordmark-name {
    display: block;
    font-size: 72px;
    letter-spacing: 8px;
    line-height: 1;
  }
  .emboss-mark .wordmark-trade {
    display: block;
    font-size: 20px;
    letter-spacing: 8px;
    text-transform: uppercase;
    margin-top: 10px;
  }
</style>
</head>
<body>
<main class="sheet">

  <section class="card card-front" aria-label="Business card front">
    <div class="accent-rule"></div>
    <div class="contact-band"></div>

    <div class="wordmark">
      <span class="wordmark-name">BRENT</span>
      <span class="wordmark-trade">Roofing &amp; Siding</span>
    </div>

    <div class="rep">
      <p class="rep-name">DANIEL HARPER</p>
      <p class="rep-title">Manager</p>
    </div>

    <ul class="contact-list">
      <li>
        <svg viewBox="0 0 12 12"><rect x="3" y="0.5" width="6" height="11" rx="1.2" fill="none" stroke="var(--ink-white)" stroke-width="1.2"/></svg>
        403-684-2093
      </li>
      <li>
        <svg viewBox="0 0 12 12"><path d="M2.5 1 L4.5 1 L5.5 4 L4 5 Q5 7.5 7 8 L8 6.5 L11 7.5 L11 9.5 Q10 11 8.5 11 Q1 9.5 1 2.5 Q1 1 2.5 1 Z" fill="var(--ink-white)"/></svg>
        403-684-2093
      </li>
      <li>
        <svg viewBox="0 0 12 12"><rect x="0.5" y="2" width="11" height="8" fill="var(--ink-white)"/><polyline points="0.5,2 6,7 11.5,2" fill="none" stroke="var(--brand-red)" stroke-width="1"/></svg>
        info@PrairieShingleWorks.com
      </li>
      <li>
        <svg viewBox="0 0 12 12"><circle cx="6" cy="6" r="5.2" fill="none" stroke="var(--ink-white)" stroke-width="1.2"/><ellipse cx="6" cy="6" rx="2.2" ry="5.2" fill="none" stroke="var(--ink-white)" stroke-width="1"/><line x1="0.8" y1="6" x2="11.2" y2="6" stroke="var(--ink-white)" stroke-width="1"/></svg>
        PrairieShingleWorks.com
      </li>
    </ul>
  </section>

  <section class="card card-back" aria-label="Business card back">
    <div class="emboss-mark">
      <span class="est">Est. 1991</span>
      <span class="wordmark-name">BRENT</span>
      <span class="wordmark-trade">Roofing &amp; Siding</span>
    </div>
  </section>

</main>
</body>
</html>
```